Technical Communications firm needs an article turned into a white paper

We want to redesign a 3-part blog series into a white paper that we can print for a conference. I've consolidated the three posts into the attached Word document.

We are looking for a light, easy to read design. Good use of graphics to support the message. I've added the graphics we used in the original post.

You can view them at
http://www.brightquillpages.com/blog/are-you-satisfied-with-your-dita-solution/

Target Market(s)

Product managers from High-tech, Finance, and Medical industries.

Industry/Entity Type

Information Technology

Colors

Designer to choose colors to be used in the design.

Requirements
Must have
• Must be modern, light, easy to read and slick design. Try to incorporate the graphics provided, but feel free to add more. Must retain the lists and tables.
• Must align with our website/brand.
• Must be easy to read. So not too busy.
• Please move all footnotes to endnotes. You'll need to rework the numbering.
Nice to have
• Awesome coverpage.
Should not have
• Hokey clipart. Not too heavy or hard to read.

```html
<!DOCTYPE html>
<html lang="en">
<head>
<meta charset="utf-8">
<title>In This White Paper – Brightquill Pages</title>
<link rel="stylesheet" href="https://fonts.googleapis.com/css2?family=Carlito:wght@400;700&display=swap">
<style>
  :root {
    --navy: #1d1a94;
    --cyan: #12a9e0;
    --rule-light: #8fd3ef;
    --text: #333333;
    --paper: #ffffff;
    --edge: #cfcfcf;
  }
  * { box-sizing: border-box; margin: 0; padding: 0; }
  html, body { width: 927px; height: 1200px; overflow: hidden; background: var(--paper); }
  body { font-family: "Carlito", "Calibri", sans-serif; color: var(--text); }

  .page {
    position: relative;
    width: 927px;
    height: 1200px;
    border: 1px solid var(--edge);
    background: var(--paper);
  }

  .brand {
    position: absolute;
    left: 84px;
    top: 58px;
    display: flex;
    align-items: center;
    gap: 12px;
  }
  .brand-mark {
    width: 84px;
    height: 84px;
    border-radius: 50%;
    background: var(--navy);
  }
  .brand-name {
    font-weight: 700;
    font-size: 27px;
    line-height: 25px;
    color: var(--navy);
    letter-spacing: 0.5px;
  }

  .margin-rule {
    position: absolute;
    left: 111px;
    top: 142px;
    width: 3px;
    height: 918px;
    background: var(--navy);
  }

  .page-number {
    position: absolute;
    left: 744px;
    top: 70px;
    width: 126px;
    height: 28px;
    border-top: 1px solid var(--rule-light);
    border-bottom: 1px solid var(--rule-light);
    text-align: center;
    font-weight: 700;
    font-size: 17px;
    line-height: 27px;
    letter-spacing: 1px;
    color: var(--navy);
  }

  .title {
    position: absolute;
    left: 178px;
    width: 693px;
    top: 164px;
    text-align: center;
    font-weight: 700;
    font-size: 33px;
    color: var(--navy);
    text-decoration: underline;
    text-underline-offset: 4px;
    text-decoration-thickness: 2px;
  }

  .intro {
    position: absolute;
    left: 178px;
    top: 217px;
    width: 694px;
    font-size: 16px;
    line-height: 22.4px;
    text-align: justify;
    text-indent: 14px;
  }

  .issues {
    position: absolute;
    left: 262px;
    top: 269px;
    width: 610px;
    list-style: none;
    font-size: 16px;
    line-height: 22.4px;
  }
  .issue {
    position: relative;
    padding-left: 25px;
    text-align: justify;
    margin-bottom: 2.5px;
  }
  .issue-label {
    font-weight: 700;
    color: var(--navy);
    text-decoration: underline;
  }
  .issue-number {
    position: absolute;
    left: 0;
    font-weight: 700;
    color: var(--navy);
    text-decoration: underline;
  }

  .dot-rule {
    position: absolute;
    left: 106px;
    top: 1072px;
  }
</style>
</head>
<body>
  <div class="page">
    <header class="brand">
      <div class="brand-mark"></div>
      <div class="brand-name">BRIGHTQUILL<br>PAGES</div>
    </header>

    <div class="page-number">PAGE 3</div>
    <div class="margin-rule"></div>

    <h1 class="title">In This White Paper</h1>

    <p class="intro">In this paper, we examine three issues impacting DITA satisfaction to help you find the best place to start making improvements.</p>

    <ol class="issues">
      <li class="issue"><span class="issue-number">1.</span><span class="issue-label">Skills Development</span> – This problem area is far and away the most pressing obstacle for a successful DITA deployment. Too often authors are left to figure out how to adapt to writing for DITA on their own.</li>
      <li class="issue"><span class="issue-number">2.</span><span class="issue-label">Technology</span> – We often hear about the failure of the technology as it relates to performance or complexity. While technology may seem the most likely culprit, it is often not the root cause of the problem.</li>
      <li class="issue"><span class="issue-number">3.</span><span class="issue-label">Management</span> – While these issues appear to be of least concern to many survey respondents, they are most likely to form the root cause of all other issues identified in the survey. This points to a general lack of awareness as to the role management should be playing in collaborative, structured authoring solutions.</li>
    </ol>

    <svg class="dot-rule" width="766" height="14" viewBox="0 0 766 14" aria-hidden="true">
      <defs>
        <pattern id="dot-pair" patternUnits="userSpaceOnUse" width="46.9" height="14">
          <circle cx="6.5" cy="7" r="6.5" fill="#1d1a94"/>
          <circle cx="29.95" cy="7" r="6.5" fill="#12a9e0"/>
        </pattern>
      </defs>
      <rect x="0" y="0" width="764" height="14" fill="url(#dot-pair)"/>
    </svg>
  </div>
</body>
</html>
```